Business card design for my company.
I would like the card's background colour to be black. You can also see our web site to get an idea of our brand. https://www.tmwhomecrafting.com.au/
- Name
- Email

```html
<!DOCTYPE html>
<html lang="en">
<head>
<meta charset="utf-8">
<title>TMW Home Crafting – Business Card</title>
<link rel="stylesheet" href="https://fonts.googleapis.com/css2?family=Poppins:wght@400;500;700&display=swap">
<style>
  :root {
    --stage: #2a2a2a;
    --card: #1c1c1c;
    --card-back: #161616;
    --green: #139443;
    --white: #ffffff;
    --pattern-light: #3a3a3a;
    --pattern-dark: #121212;
  }
  * { box-sizing: border-box; margin: 0; padding: 0; }
  html, body {
    width: 1200px; height: 800px; overflow: hidden;
    background: var(--stage);
    font-family: "Poppins", sans-serif;
  }
  .stage {
    width: 1200px; height: 800px;
    display: flex; flex-direction: column;
    align-items: center; justify-content: center; gap: 40px;
  }
  .card {
    position: relative;
    width: 600px; height: 343px;
    border-radius: 18px;
    overflow: hidden;
    box-shadow: 0 10px 30px rgba(0,0,0,.45);
  }
  .card-front { background: var(--card); }
  .card-back { background: var(--card-back); }

  .brand {
    position: absolute; left: 330px; top: 60px;
    display: flex; align-items: center; gap: 12px;
    color: var(--white); font-weight: 700;
    font-size: 24px; line-height: 1.1; letter-spacing: 1px;
  }
  .brand-square { width: 16px; height: 16px; background: var(--green); flex: none; }

  .divider { position: absolute; inset: 0; width: 600px; height: 343px; }

  .person { position: absolute; left: 40px; top: 168px; }
  .person-name {
    color: var(--green); font-weight: 700; font-size: 27px;
    letter-spacing: .5px; line-height: 1.1;
  }
  .person-role { color: var(--white); font-size: 15px; font-weight: 500; margin-top: 2px; }

  .contacts {
    position: absolute; left: 40px; top: 268px;
    list-style: none; color: var(--white); font-size: 13.5px;
  }
  .contacts li { display: flex; align-items: center; gap: 10px; line-height: 24px; }
  .contacts svg { width: 13px; height: 13px; flex: none; }

  .web-band {
    position: absolute; right: 0; bottom: 0;
    width: 300px; height: 42px;
    background: var(--green);
    clip-path: polygon(14px 0, 100% 0, 100% 100%, 0 100%);
    color: var(--white); font-size: 14px; font-weight: 500;
    display: flex; align-items: center; justify-content: center;
  }

  .logo-pattern {
    position: absolute; inset: 0;
    background: linear-gradient(120deg, var(--pattern-light), var(--pattern-dark) 70%);
  }
  .back-brand {
    position: absolute; right: 30px; bottom: 36px;
    display: flex; align-items: center; gap: 8px;
    color: var(--white); font-weight: 700; font-size: 13px; letter-spacing: .5px;
  }
  .back-brand .brand-square { width: 10px; height: 10px; }
</style>
</head>
<body>
<main class="stage">
  <section class="card card-front" aria-label="Card front">
    <div class="brand">
      <span class="brand-square"></span>
      <span>TMW<br>HOME CRAFTING</span>
    </div>

    <svg class="divider" viewBox="0 0 600 343" aria-hidden="true">
      <line x1="40" y1="262" x2="575" y2="128" stroke="var(--green)" stroke-width="1.2"/>
    </svg>

    <div class="person">
      <h1 class="person-name">SAM WHITFORD</h1>
      <p class="person-role">General Manager</p>
    </div>

    <ul class="contacts">
      <li>
        <svg viewBox="0 0 24 24" aria-hidden="true"><path fill="var(--green)" d="M6.6 10.8a15 15 0 0 0 6.6 6.6l2.2-2.2c.3-.3.7-.4 1-.2 1.1.4 2.3.6 3.6.6.6 0 1 .4 1 1V20c0 .6-.4 1-1 1A17 17 0 0 1 3 4c0-.6.4-1 1-1h3.5c.6 0 1 .4 1 1 0 1.3.2 2.5.6 3.6.1.3 0 .7-.2 1z"/></svg>
        <span>0400 123 456</span>
      </li>
      <li>
        <svg viewBox="0 0 24 24" aria-hidden="true"><path fill="var(--green)" d="M2 5h20v14H2z"/><path fill="none" stroke="var(--card)" stroke-width="1.8" d="M2 5l10 8 10-8"/></svg>
        <span>info@tmwhomecrafting.com.au</span>
      </li>
    </ul>

    <div class="web-band">www.tmwhomecrafting.com.au</div>
  </section>

  <section class="card card-back" aria-label="Card back">
    <div class="logo-pattern" role="img" aria-label="Repeating tone-on-tone brand pattern in glossy dark grey"></div>
    <div class="back-brand">
      <span class="brand-square"></span>
      <span>TMW HOME CRAFTING</span>
    </div>
  </section>
</main>
</body>
</html>
```